Business Card - connecting 2 souls and beggining the journey of self discovery

Logo on the front
with tag line

On the back list of services and contact details

Seminars
workshops
Coaching
podcasts

Darren Whitlow
Health & Wellbeing Life Coach
0491 372 615
darren@brightcoreliving.example
brightcoreliving.example

Industry/Entity Type

Life Coaching

Contact Information for Business Card

I like the use of colour from the logo to be used. I'm not a fan of white.

Requirements
Must have
• My tagline: The journey home starts with you
Nice to have
• Use of colour that is in the Brightcore Living logo

```html
<!DOCTYPE html>
<html lang="en">
<head>
<meta charset="utf-8">
<title>Brightcore Living – Business Card</title>
<link rel="stylesheet" href="https://fonts.googleapis.com/css2?family=Open+Sans:wght@400;600;700&display=swap">
<style>
  :root {
    --backdrop: #3a332f;
    --card: #1b1b1c;
    --card-edge: #262627;
    --text-light: #e9e9e9;
    --text-grey: #8c8c8c;
    --text-muted: #a9a9a9;
    --accent-green: #4fbf8a;
    --accent-coral: #e8566a;
    --accent-violet: #8a4fb8;
    --divider: #5a5a5a;
  }
  * { box-sizing: border-box; margin: 0; padding: 0; }
  html, body {
    width: 1200px; height: 864px; overflow: hidden;
    background: var(--backdrop);
    font-family: "Open Sans", Arial, sans-serif;
  }
  .stage { position: relative; width: 1200px; height: 864px; }
  .card {
    position: absolute; top: 282px;
    width: 520px; height: 300px;
    background: var(--card);
    border: 1px solid var(--card-edge);
    border-radius: 4px;
  }
  .card--front { left: 60px; }
  .card--back { left: 620px; }

  /* Front */
  .front-brand {
    position: absolute; top: 52px; left: 0; right: 0;
    display: flex; flex-direction: column; align-items: center;
  }
  .brand-dot {
    width: 112px; height: 112px; border-radius: 50%;
    background: var(--accent-violet);
  }
  .front-brand .brand-name {
    margin-top: 16px;
    font-size: 22px; font-weight: 600; color: var(--text-light);
    letter-spacing: 0.5px;
  }
  .services {
    position: absolute; bottom: 40px; left: 0; right: 0;
    text-align: center; font-size: 14px; color: var(--text-muted);
  }
  .services .sep { color: var(--accent-green); margin: 0 6px; }

  /* Back */
  .back-identity {
    position: absolute; left: 26px; top: 96px; width: 220px;
    display: flex; flex-direction: column; align-items: flex-start;
  }
  .back-identity .brand-dot--small {
    width: 44px; height: 44px; border-radius: 50%;
    background: var(--accent-violet); margin: 0 0 12px 72px;
  }
  .back-identity .brand-name {
    font-size: 19px; font-weight: 600; color: var(--text-grey);
    letter-spacing: -0.3px;
  }
  .tagline { margin-top: 2px; font-size: 11.5px; color: var(--text-grey); }
  .divider {
    position: absolute; left: 256px; top: 88px;
    width: 1px; height: 110px; background: var(--divider);
  }
  .contact { position: absolute; left: 272px; top: 108px; }
  .person-name {
    font-size: 17px; font-weight: 700; color: var(--accent-green);
    text-transform: uppercase; letter-spacing: 0.3px;
  }
  .person-role {
    font-size: 13px; font-weight: 700; color: var(--accent-coral);
    text-transform: uppercase; letter-spacing: 0.3px; margin-bottom: 8px;
  }
  .contact-list { list-style: none; }
  .contact-list li {
    display: flex; align-items: center; gap: 6px;
    font-size: 12.5px; color: var(--text-light); line-height: 18px;
  }
  .contact-list svg { width: 11px; height: 11px; fill: var(--accent-green); flex: none; }
</style>
</head>
<body>
<main class="stage">
  <section class="card card--front" aria-label="Card front">
    <div class="front-brand">
      <span class="brand-dot"></span>
      <span class="brand-name">Brightcore Living</span>
    </div>
    <p class="services">Seminars<span class="sep">•</span>Workshops<span class="sep">•</span>Coaching<span class="sep">•</span>Podcasts</p>
  </section>

  <section class="card card--back" aria-label="Card back">
    <div class="back-identity">
      <span class="brand-dot--small"></span>
      <span class="brand-name">Brightcore Living</span>
      <span class="tagline">The journey home starts with you</span>
    </div>
    <span class="divider"></span>
    <div class="contact">
      <p class="person-name">Darren Whitlow</p>
      <p class="person-role">Health &amp; Wellbeing Life Coach</p>
      <ul class="contact-list">
        <li>
          <svg viewBox="0 0 24 24" aria-hidden="true"><path d="M6.6 10.8a15 15 0 0 0 6.6 6.6l2.2-2.2a1 1 0 0 1 1-.25 11.4 11.4 0 0 0 3.6.57 1 1 0 0 1 1 1V20a1 1 0 0 1-1 1A17 17 0 0 1 3 4a1 1 0 0 1 1-1h3.5a1 1 0 0 1 1 1c0 1.25.2 2.45.57 3.57a1 1 0 0 1-.25 1z"/></svg>
          0491 372 615
        </li>
        <li>
          <svg viewBox="0 0 24 24" aria-hidden="true"><path d="M2 5h20v14H2z M3.5 6.5 12 13l8.5-6.5" fill="none" stroke="#4fbf8a" stroke-width="2.4"/></svg>
          darren@brightcoreliving.example
        </li>
        <li>
          <svg viewBox="0 0 24 24" aria-hidden="true"><path d="M12 2a7 7 0 0 0-7 7c0 5.25 7 13 7 13s7-7.75 7-13a7 7 0 0 0-7-7zm0 9.5A2.5 2.5 0 1 1 12 6.5a2.5 2.5 0 0 1 0 5z"/></svg>
          www.brightcoreliving.example
        </li>
      </ul>
    </div>
  </section>
</main>
</body>
</html>
```